www.marvenholt.com

Updating website so looks futristic but yet business like and easy to navigate, essentially a good landing page with a cool picture summing up what we do, and links to the following pages, all other pages on site to be updated, Exclusive Distributor of Brisk Forge Unique Fitness Equipment Products in UK & Ireland, www.crestvolley.co.uk Exclusive Partners & Distributors Of Crest Volley - Obstacle Races - Obstacle Hire - Obstacle Training - Adventure Events, www.goplumwick.co.uk Adventures That Inspire. We also Health Club / Facillity Consultancy

```html
<!DOCTYPE html>
<html lang="en">
<head>
<meta charset="utf-8">
<title>Marven Holt – Health, Wellness, Fitness Consultants</title>
<link rel="stylesheet" href="https://fonts.googleapis.com/css2?family=Open+Sans:wght@400;600;700&family=Mulish:wght@400;600&display=swap">
<style>
:root{
  --orange:#fd5a1e;
  --orange-deep:#e94c12;
  --charcoal:#333333;
  --ink:#2b2b2b;
  --text:#444444;
  --muted:#7a7a7a;
  --white:#ffffff;
  --line:#d9d9d9;
}
*{box-sizing:border-box;margin:0;padding:0}
html,body{width:1200px;height:2946px;overflow:hidden}
body{position:relative;font-family:"Mulish",sans-serif;color:var(--text);background:var(--white)}
.abs{position:absolute}
h2{font-family:"Open Sans",sans-serif;font-weight:600}

/* top bar */
.topbar{left:0;top:0;width:1200px;height:41px;background:var(--charcoal);color:var(--white);font-size:15px}
.topbar .contact{left:78px;top:10px;display:flex;align-items:center;gap:10px}
.topbar .contact span{margin-right:28px}
.topbar .social{right:70px;top:12px;display:flex;gap:26px}
.topbar .social i{display:block;width:16px;height:16px;border-radius:50%;background:#9a9a9a}

/* header */
.header{left:0;top:41px;width:1200px;height:102px;background:var(--white)}
.brand{left:78px;top:20px}
.brand-name{font-family:"Open Sans",sans-serif;font-weight:400;font-size:36px;letter-spacing:2px;text-transform:uppercase;color:#666;line-height:1}
.brand-tag{font-family:"Open Sans",sans-serif;font-size:14px;color:#888;margin-top:6px}
.product-link{right:82px;top:22px;font-family:"Open Sans",sans-serif;font-size:19px;color:var(--ink);text-transform:uppercase}
.nav{right:80px;top:60px;display:flex;gap:26px;font-family:"Open Sans",sans-serif;font-size:18px;color:var(--ink)}

/* hero */
.hero{left:0;top:143px;width:1200px;height:586px;background:linear-gradient(110deg,#5b6a78 0%,#b7c3cc 30%,#e9e3de 50%,#cfd9e2 70%,#2e63b5 100%)}
.hours-tab{left:295px;top:143px}
.hero-title{left:0;top:568px;width:1200px;text-align:center;font-family:"Open Sans",sans-serif;font-weight:700;font-size:42px;color:#111}

/* services */
.services{left:0;top:729px;width:1200px;height:520px;border-bottom:1px solid var(--orange)}
.services .photo-panel{left:0;top:0;width:580px;height:520px;background:var(--orange)}
.services .people{left:100px;top:18px;width:450px;height:502px;background:linear-gradient(180deg,#b66c48,#7a3f25 55%,#1f2430);border-radius:40px 40px 0 0}
.services .pointer{left:580px;top:243px}
.service{left:640px;display:flex;gap:20px}
.service h3{font-family:"Open Sans",sans-serif;font-weight:400;font-size:32px;color:#444;line-height:1.1}
.service p{font-size:15.5px;line-height:25px;color:#555;width:320px}
.service a{font-family:"Open Sans",sans-serif;font-weight:700;font-size:15px;color:var(--orange);text-decoration:none}

/* experts */
.experts{left:0;top:1249px;width:1200px;height:358px}
.experts h2{position:absolute;left:0;top:60px;width:1200px;text-align:center;font-size:38px;color:var(--ink)}
.experts p{position:absolute;left:142px;top:114px;width:916px;text-align:center;font-size:15.5px;line-height:25.3px;color:#444}

/* team */
.team{left:0;top:1607px;width:1200px;height:436px;background:var(--orange)}
.team h2{position:absolute;left:0;top:36px;width:1200px;text-align:center;font-size:38px;color:var(--white)}
.member-photo{left:253px;top:98px;width:269px;height:290px;background:linear-gradient(160deg,#4a6b8e,#c7a089 45%,#1c2840);border:1px solid #fff}
.member-card{left:522px;top:121px;width:427px;height:246px;border:1px solid #fff;padding:3px}
.member-card .inner{border:1px solid #fff;height:100%;padding:14px 16px 0 16px;color:var(--white)}
.member-card h3{font-family:"Open Sans",sans-serif;font-weight:600;font-size:27px;line-height:1.1}
.member-card .role{font-family:"Open Sans",sans-serif;font-size:15px;margin:2px 0 2px}
.member-card p{font-size:15px;line-height:24.5px}
.slider-arrow{top:228px}

/* testimonials */
.testimonials{left:0;top:2043px;width:1200px;height:444px}
.testimonials h2{position:absolute;left:0;top:36px;width:1200px;text-align:center;font-size:38px;color:var(--ink)}
.testimonials .badge{left:553px;top:118px;width:94px;height:94px;border-radius:50%;background:var(--orange-deep);border:5px solid #222}
.testimonials blockquote{position:absolute;left:165px;top:232px;width:870px;text-align:center;font-size:15.5px;line-height:25px;color:#555}
.tiny-arrow{top:252px;width:30px;height:30px;background:#e3e3e3}

/* contact */
.contact-sec{left:0;top:2487px;width:1200px;height:406px;background:var(--charcoal)}
.contact-sec h2{position:absolute;left:0;top:44px;width:1200px;text-align:center;font-size:38px;color:var(--white)}
.field{position:absolute;left:79px;background:var(--white);border:1px solid #ccc;font-size:15px;color:#777;padding:10px 14px}
.send{position:absolute;left:526px;top:237px;width:136px;height:114px;background:var(--orange);color:var(--white);font-family:"Open Sans",sans-serif;font-weight:600;font-size:18px;text-align:center;padding-top:30px}
.info{position:absolute;left:724px;color:var(--white);font-size:15px;line-height:23px;display:flex;gap:22px}
.info svg{flex:none}

/* footer */
.footer{left:0;top:2893px;width:1200px;height:53px;background:var(--orange);color:var(--white);font-size:15px;text-align:center;line-height:53px}
</style>
</head>
<body>

<div class="abs topbar">
  <div class="abs contact">
    <svg width="18" height="18" viewBox="0 0 24 24"><path fill="#fff" d="M6.6 10.8a15.1 15.1 0 0 0 6.6 6.6l2.2-2.2c.3-.3.7-.4 1-.2 1.1.4 2.3.6 3.6.6.6 0 1 .4 1 1V20c0 .6-.4 1-1 1A17 17 0 0 1 3 4c0-.6.4-1 1-1h3.5c.6 0 1 .4 1 1 0 1.3.2 2.5.6 3.6.1.3 0 .7-.2 1z"/></svg>
    <span>Phone: 07700-900418</span><span>Office: 01632-960551</span>
  </div>
  <div class="abs social" aria-label="Social links"><i></i><i></i><i></i></div>
</div>

<header class="abs header">
  <div class="abs brand">
    <div class="brand-name">Marven Holt</div>
    <div class="brand-tag">Health , Wellness , Fitness , Consultants</div>
  </div>
  <div class="abs product-link">Brisk Forge</div>
  <nav class="abs nav"><span>Home</span><span>Health</span><span>Wellness</span><span>Fitness</span><span>Team</span><span>Testimonials</span><span>contact</span></nav>
</header>

<section class="abs hero" role="img" aria-label="Photo of a woman training on a gym pull-down machine"></section>
<svg class="abs hours-tab" width="608" height="66" viewBox="0 0 608 66">
  <polygon points="0,0 608,0 364,60 244,60" fill="#fd5a1e" opacity=".92"/>
  <text x="304" y="37" text-anchor="middle" font-family="Open Sans, sans-serif" font-size="17" fill="#fff">OPEN HOURS</text>
  <polygon points="296,46 312,46 304,54" fill="#fff"/>
</svg>
<div class="abs hero-title">Fit is not a destination, it is a way</div>

<section class="abs services">
  <div class="abs photo-panel"></div>
  <div class="abs people" role="img" aria-label="Photo of a fit man and woman holding dumbbells"></div>
  <svg class="abs pointer" width="22" height="40" viewBox="0 0 22 40"><polygon points="0,0 22,20 0,40" fill="#fd5a1e"/></svg>

  <div class="abs service" style="top:78px">
    <svg width="62" height="62" viewBox="0 0 64 64"><path d="M32 58 8 34A14 14 0 0 1 32 14a14 14 0 0 1 24 20z" fill="#fd5a1e"/><polyline points="12,34 24,34 28,26 33,42 37,30 40,34 52,34" fill="none" stroke="#fff" stroke-width="3"/></svg>
    <div><h3>Health</h3><p>Lorem Ipsum is simply dummy text of the printing and typesetting industry.</p><a>WATCH VIDEO</a></div>
  </div>
  <div class="abs service" style="top:226px">
    <svg width="62" height="62" viewBox="0 0 64 64" fill="none" stroke="#fd5a1e" stroke-width="3" stroke-linecap="round"><circle cx="32" cy="22" r="5" fill="#fd5a1e"/><path d="M20 30l12 6 12-6M32 36v14M32 50l-6 6M32 50l6 6"/><path d="M32 6v6M14 14l4 4M50 14l-4 4M8 32h6M50 32h6"/></svg>
    <div><h3>Wellness</h3><p>Lorem Ipsum is simply dummy text of the printing and typesetting industry.</p><a>WATCH VIDEO</a></div>
  </div>
  <div class="abs service" style="top:370px">
    <svg width="62" height="62" viewBox="0 0 64 64" fill="none" stroke="#fd5a1e" stroke-width="3.5"><g transform="rotate(-45 32 32)"><rect x="6" y="22" width="8" height="20" rx="2"/><rect x="14" y="18" width="8" height="28" rx="2"/><rect x="42" y="18" width="8" height="28" rx="2"/><rect x="50" y="22" width="8" height="20" rx="2"/><line x1="22" y1="32" x2="42" y2="32"/></g></svg>
    <div><h3>Fitness</h3><p>Lorem Ipsum is simply dummy text of the printing and typesetting industry.</p><a>WATCH VIDEO</a></div>
  </div>
</section>

<section class="abs experts">
  <h2>We Are Experts In The Industry</h2>
  <p>Marven Holt are leading consultants to the Health, Wellness and Fitness industry, with over 25 years experience working with some of the biggest global worldwide brands from equipment providers and facility operators to mass participation events and obstacle course races. Marven Holt is a multi disciplined business specialising in helping brands grow through insight, strategy creation and valuable sector collaboration, recent clients include the exclusive distribution of Brisk Forge bodyweight training products for the UK and Ireland, exclusive distribution of fitness app Pulse Ledger, Ridgeline Trek Race, Crest Volley, Vantor Fitness, Kestra UK, Hollin Leisure, Active Brackwell, Dunmere Community Leisure, Trim Path Coach, Strevlo and Northvale Health.The Marven Holt team specialise in a bespoke, consultative approach for each project and pride ourselves in our attention to detail with passion and dedication.</p>
</section>

<section class="abs team">
  <h2>Our Team</h2>
  <div class="abs member-photo" role="img" aria-label="Portrait photo of the founder"></div>
  <div class="abs member-card"><div class="inner">
    <h3>Rowan Pell</h3>
    <div class="role">Founder / Director</div>
    <p>Marven Holt long term success depends on the talents commitment and shared values of our people, Marven Holt is made of a unique hand picked team that will ensure the best possible service is delivered, as a company were passionate about delivering the best for our clients... &raquo;</p>
  </div></div>
  <svg class="abs slider-arrow" style="left:76px" width="20" height="40" viewBox="0 0 20 40"><polyline points="16,4 4,20 16,36" fill="none" stroke="#fff" stroke-width="4"/></svg>
  <svg class="abs slider-arrow" style="left:1102px" width="20" height="40" viewBox="0 0 20 40"><polyline points="4,4 16,20 4,36" fill="none" stroke="#fff" stroke-width="4"/></svg>
</section>

<section class="abs testimonials">
  <h2>Testimonials</h2>
  <div class="abs badge" aria-label="Partner badge"></div>
  <svg class="abs tiny-arrow" style="left:76px" viewBox="0 0 30 30"><polyline points="18,8 11,15 18,22" fill="none" stroke="#fd5a1e" stroke-width="3"/></svg>
  <svg class="abs tiny-arrow" style="left:1094px" viewBox="0 0 30 30"><polyline points="12,8 19,15 12,22" fill="none" stroke="#fd5a1e" stroke-width="3"/></svg>
  <blockquote>Ridgeline Trek Race and Marven Holt first collaborated in 2015. Rowan and the Marven Holt team have showed impeccable drive, commitment, passion and integrity throughout our partnership. With the help of the Marven Holt team Ridgeline Race have gained huge success in the UK in 2015 and we are in great shape for 2016. Their ability to go to market quickly, professionally, with tenacity and high energy enables me to personally recommend the Marven Holt organisation to anyone, or any company who requires a genuine, successful business collaboration and wants a great return on their investment “Highly Recommended”<br>Calder Voss – Ridgeline Race CEO &amp; Founder of Ridgeline Race</blockquote>
</section>

<section class="abs contact-sec">
  <h2>Keep Contact With Us</h2>
  <div class="field" style="top:123px;width:579px;height:45px">Name</div>
  <div class="field" style="top:178px;width:579px;height:47px">Email Id</div>
  <div class="field" style="top:237px;width:432px;height:114px">Message</div>
  <div class="send">
    <svg width="24" height="22" viewBox="0 0 24 22"><path d="M1 10 23 1 18 21 11 14 19 5 8 12z" fill="#fff"/></svg>
    <div>SEND</div>
  </div>
  <div class="info" style="top:152px"><svg width="22" height="26" viewBox="0 0 24 28"><path d="M12 1a9 9 0 0 0-9 9c0 7 9 17 9 17s9-10 9-17a9 9 0 0 0-9-9zm0 12.5a3.5 3.5 0 1 1 0-7 3.5 3.5 0 0 1 0 7z" fill="#fd5a1e"/></svg><div>The Granary Millbrook UK &amp; Ireland</div></div>
  <div class="info" style="top:193px"><svg width="26" height="26" viewBox="0 0 24 24"><path fill="#fd5a1e" d="M6.6 10.8a15.1 15.1 0 0 0 6.6 6.6l2.2-2.2c.3-.3.7-.4 1-.2 1.1.4 2.3.6 3.6.6.6 0 1 .4 1 1V20c0 .6-.4 1-1 1A17 17 0 0 1 3 4c0-.6.4-1 1-1h3.5c.6 0 1 .4 1 1 0 1.3.2 2.5.6 3.6.1.3 0 .7-.2 1z"/></svg><div>Phone: 07700-900418<br>Office: 01632-960551</div></div>
  <div class="info" style="top:259px"><svg width="26" height="20" viewBox="0 0 26 20"><rect x="1.5" y="1.5" width="23" height="17" fill="none" stroke="#fd5a1e" stroke-width="2.5"/><polyline points="2,2 13,11 24,2" fill="none" stroke="#fd5a1e" stroke-width="2.5"/></svg><div>Web: www.marvenholt.com<br>E-mail:&nbsp; info@marvenholt.com</div></div>
</section>

<footer class="abs footer">2017 ©Marven Holt - All Rights Reserved.</footer>

</body>
</html>
```